Brimsett Gardening Fresh New Website

We are looking to create a simple fresh website for our landscaping business. The website should appeal to a 'high end' audience. We deal with a lot of Embassies and affluent clients who have extremely large gardens that are meticulously maintained. The site is about communicating our excellent landscaping and customer service skills and encouraging new clients to reach out and engage us to take care of their gardens.

The website is basically going to be our business card, it will have almost no functionality other than two 'contact us' forms, one for smaller clients and one for more detailed projects.

The website will not have a lot of written content and will have to show photos of beautifully landscaped gardens.

The main logo in black will influence the site, however, we are open to all suggestions.

We are expecting to have the following pages:
Home Page
Services
About Us
Contact Us
Showcase (photo gallery of our work)

We need someone who can code it to wordpress and be available for minor changes over a number of days. They will be simple tweaks.

```html
<!DOCTYPE html>
<html lang="en">
<head>
<meta charset="utf-8">
<title>Brimsett Gardening</title>
<link href="https://fonts.googleapis.com/css2?family=Cinzel:wght@400;600&family=Montserrat:wght@400;500;600;700&display=swap" rel="stylesheet">
<style>
:root{
  --gold:#d6a92c;
  --gold-light:#ecc640;
  --gold-dark:#b7861d;
  --ink:#1b1b1b;
  --dark:#1d1d1d;
  --text:#555;
  --card:#f1f1f1;
  --white:#fff;
  --serif:'Cinzel',serif;
  --sans:'Montserrat',sans-serif;
}
*{box-sizing:border-box;margin:0;padding:0}
html,body{width:1200px;height:3968px;overflow:hidden}
body{position:relative;background:var(--white);font-family:var(--sans);color:var(--ink)}
.abs{position:absolute}
.gold-grad{background:linear-gradient(90deg,var(--gold-dark),var(--gold-light))}
.btn{position:absolute;display:flex;align-items:center;justify-content:center;color:var(--white);font:700 11px/1 var(--sans);letter-spacing:1.2px;text-transform:uppercase;background:linear-gradient(90deg,var(--gold-dark),var(--gold-light))}
.h-serif{font-family:var(--serif);font-weight:400;color:var(--ink)}
.section-title{position:absolute;left:0;width:1200px;text-align:center;font:400 34px/1 var(--serif);color:var(--ink);letter-spacing:1px}

.topbar{left:0;top:0;width:1200px;height:37px}
.topbar .item{position:absolute;top:0;height:37px;display:flex;align-items:center;gap:8px;color:var(--white);font:500 10.5px/1 var(--sans)}
.ico{width:15px;height:15px;border-radius:50%;background:var(--ink);display:inline-block;flex:none}
.topbar .social{position:absolute;top:11px;display:flex;gap:9px}

.hero{left:0;top:37px;width:1200px;height:575px}
.nav{position:absolute;top:62px}
.nav a{position:absolute;top:0;color:var(--white);font:600 12px/1 var(--sans);letter-spacing:1px;text-decoration:none;white-space:nowrap}
.nav a.active{color:var(--gold)}
.logo{position:absolute;text-align:center;font-family:var(--serif);font-weight:400;color:var(--gold)}
.hero-title{left:0;top:226px;width:1200px;text-align:center;font:400 42px/48px var(--serif);color:var(--white);letter-spacing:1.5px}
.hero-sub{left:0;top:329px;width:1200px;text-align:center;font:500 13px/1 var(--sans);color:var(--white)}

.about-bg{left:0;top:600px;width:1200px;height:490px;background:radial-gradient(ellipse at 45% 85%,#d9d9d9 0%,#f4f4f4 45%,#fff 75%)}
.about-title{left:722px;top:682px;font:400 33px/38px var(--serif);color:var(--ink)}
.about-text{left:722px;top:767px;width:360px;font:400 10.5px/15px var(--sans);color:var(--text)}

.split{top:1098px;height:236px}
.split .photo{position:absolute;top:0;height:236px}
.split .body{position:absolute;top:0;height:236px;background:var(--dark);color:var(--white)}
.split h3{position:absolute;font:400 26px/1 var(--serif);letter-spacing:1.5px;color:var(--white)}
.split p{position:absolute;font:400 10px/15px var(--sans);color:#ddd}

.svc{position:absolute;background:var(--card)}
.svc .img{position:absolute;left:0;top:0;width:100%}
.svc .name{position:absolute;left:0;width:100%;text-align:center;font:600 14px/1 var(--sans);color:var(--ink)}
.svc .arrow{position:absolute;left:50%;margin-left:-9px}
.svc.featured{background:linear-gradient(90deg,var(--gold-dark),var(--gold-light))}
.badge{position:absolute;left:50%;margin-left:-30px;width:60px;height:60px;border-radius:50%;background:linear-gradient(135deg,var(--gold-dark),var(--gold-light));border:3px solid var(--white)}
.badge.light{background:var(--white);border-color:#e3c06a}

.testi-band{left:0;top:2160px;width:1200px;height:385px;background:linear-gradient(90deg,#c99a25 0%,#dcae33 50%,#efc93d 100%)}
.testi-title{color:var(--white)}
.tcard{position:absolute;top:2261px;width:298px;height:227px;background:var(--white);box-shadow:0 4px 10px rgba(0,0,0,.15)}
.tcard .avatar{position:absolute;left:22px;top:28px;width:46px;height:46px;border-radius:50%;background:linear-gradient(160deg,#9aa3ab,#4a5159)}
.tcard .who{position:absolute;left:84px;top:42px;font:600 13px/1 var(--sans);color:var(--ink)}
.tcard .stars{position:absolute;left:84px;top:59px;color:var(--gold);font-size:11px;letter-spacing:2px}
.tcard p{position:absolute;left:22px;top:100px;width:262px;font:400 10px/15px var(--sans);color:#444}
.tcard .quote{position:absolute;right:14px;bottom:12px;font:700 64px/1 Georgia,serif;color:#d2d2d2;height:40px;overflow:hidden}
.tnav{position:absolute;top:2368px;width:20px;height:20px;border-radius:50%;background:var(--white);display:flex;align-items:center;justify-content:center}

.proj{position:absolute;width:306px;height:225px;overflow:hidden;border-radius:6px}
.proj .img{position:absolute;inset:0}
.proj .label{position:absolute;left:0;bottom:0;width:100%;height:36px;background:rgba(20,20,20,.55);border-top:2px solid var(--gold);color:var(--white);font:700 13.5px/34px var(--sans);text-align:center}

.contact-title{left:123px;top:3262px;font:400 34px/1 var(--serif)}
.contact-sub{left:123px;top:3302px;width:370px;font:400 10.5px/15px var(--sans);color:var(--text)}
.field{position:absolute;left:123px;width:359px;height:32px;border:1px solid #999;background:var(--white);font:400 10.5px/1 var(--sans);color:#777;padding:10px 18px}
.contact-bg{left:420px;top:3240px;width:780px;height:480px;background:radial-gradient(ellipse at 45% 80%,#dcdcdc 0%,#f3f3f3 40%,rgba(255,255,255,0) 70%)}

.footer{left:0;top:3734px;width:1200px;height:209px;background:var(--dark)}
.footer .rule{position:absolute;top:38px;width:1px;height:150px;background:#555}
.footer h4{position:absolute;top:40px;font:400 15px/1 var(--serif);color:var(--white);letter-spacing:1px}
.footer .links a{position:absolute;font:400 9.5px/1 var(--sans);color:#ddd;text-decoration:none}
.footer .line{position:absolute;display:flex;align-items:flex-start;gap:8px;font:400 9.5px/14px var(--sans);color:#ddd}
.footer .line .dot{width:16px;height:16px;border-radius:50%;background:var(--gold);flex:none;margin-top:-1px}
.footer .about-f{position:absolute;left:126px;top:138px;width:205px;font:400 9.5px/14px var(--sans);color:#ddd}
.copyright{left:0;top:3943px;width:1200px;height:25px;display:flex;align-items:center;justify-content:center;font:400 9.5px/1 var(--sans);color:var(--ink)}
</style>
</head>
<body>

<div class="abs topbar gold-grad">
  <div class="item" style="left:123px"><span class="ico"></span>(405) 555-0148</div>
  <div class="item" style="left:284px"><span class="ico"></span>info@brimsettgardening.com</div>
  <div class="item" style="left:512px"><span class="ico"></span>1187 Larkspur Ave #310, Oklahoma City, OK 73120</div>
  <div class="social" style="left:970px">
    <svg width="14" height="14" viewBox="0 0 14 14"><circle cx="6" cy="6" r="4.5" fill="none" stroke="#1b1b1b" stroke-width="1.6"/><line x1="9.3" y1="9.3" x2="13" y2="13" stroke="#1b1b1b" stroke-width="1.6"/></svg>
    <span class="ico"></span><span class="ico"></span><span class="ico"></span>
  </div>
</div>

<svg class="abs hero" viewBox="0 0 1200 575" role="img" aria-label="Photograph of a large manicured garden with clipped hedges and beds of yellow flowers">
  <defs>
    <linearGradient id="heroGrad" x1="0" y1="0" x2="0" y2="1">
      <stop offset="0" stop-color="#121810"/>
      <stop offset="0.45" stop-color="#2b3a1c"/>
      <stop offset="0.75" stop-color="#4d5a1e"/>
      <stop offset="1" stop-color="#a8921c"/>
    </linearGradient>
    <linearGradient id="goldLine" x1="0" y1="0" x2="1" y2="0">
      <stop offset="0" stop-color="#b7861d"/><stop offset="1" stop-color="#ecc640"/>
    </linearGradient>
  </defs>
  <polygon points="0,0 1200,0 1200,418 600,568 0,418" fill="url(#heroGrad)"/>
  <polyline points="0,418 600,568 1200,418" fill="none" stroke="url(#goldLine)" stroke-width="6"/>
</svg>

<div class="logo" style="left:118px;top:42px;width:82px">
  <svg width="22" height="30" viewBox="0 0 22 30"><circle cx="11" cy="15" r="9" fill="none" stroke="#d6a92c" stroke-width="1.4"/></svg>
  <div style="font-size:10.5px;letter-spacing:3.5px;line-height:13px">BRIMSETT</div>
  <div style="font-size:5.5px;letter-spacing:2.6px;line-height:8px">GARDENING</div>
</div>

<nav class="nav" style="left:0;top:62px">
  <a class="active" style="left:449px">HOME</a>
  <a style="left:556px">SERVICES</a>
  <a style="left:671px">ABOUT US</a>
  <a style="left:794px">OUR PROJECT</a>
</nav>
<div class="btn" style="left:924px;top:52px;width:122px;height:34px;font-size:12px">CONTACT US</div>

<svg class="abs" style="left:578px;top:152px" width="44" height="44" viewBox="0 0 44 44">
  <circle cx="22" cy="22" r="20" fill="none" stroke="#fff" stroke-width="2"/>
</svg>
<div class="abs hero-title">LANDSCAPING BUSINESS<br>FOR LARGE GARDENS</div>
<div class="abs hero-sub">large gardens that are meticulously maintained.</div>
<div class="btn" style="left:496px;top:362px;width:208px;height:37px">DISCOVER OUR SERVICES</div>

<div class="abs about-bg"></div>
<svg class="abs" style="left:126px;top:588px" width="350" height="462" viewBox="0 0 350 462" role="img" aria-label="Photograph of a smiling gardener kneeling with a potted plant, framed in a gold drop shape">
  <defs>
    <linearGradient id="frameGold" x1="0" y1="0" x2="1" y2="1">
      <stop offset="0" stop-color="#b7861d"/><stop offset="0.5" stop-color="#ecc640"/><stop offset="1" stop-color="#b7861d"/>
    </linearGradient>
    <linearGradient id="aboutPhoto" x1="0" y1="0" x2="0" y2="1">
      <stop offset="0" stop-color="#5f7a3c"/><stop offset="0.5" stop-color="#2f4f2a"/><stop offset="1" stop-color="#8a8f7c"/>
    </linearGradient>
  </defs>
  <path d="M175 4 C240 100 346 190 346 290 A171 171 0 0 1 4 290 C4 190 110 100 175 4 Z" fill="#fff" stroke="url(#frameGold)" stroke-width="9"/>
  <path d="M175 40 C228 120 318 200 318 290 A143 143 0 0 1 32 290 C32 200 122 120 175 40 Z" fill="url(#aboutPhoto)"/>
</svg>
<div class="abs about-title">ABOUT BRIMSETT<br>GARDENING</div>
<p class="abs about-text">Greenmark Landscape Management, Inc. offers green solutions for our clients. We strive to make responsible changes, using permeable hardscape materials, reduce water waste, and plant more sustainable landscapes. We often collaborate with our son, Daniel P. Whitcombe, who specializes in 3D rendering and auto cad landscape design. Elise views the garden as an ever changing narrative that mirrors life, believing that the garden is a place for curiosity and play.Built on a family tradition of caring, we are driven by a passion to exceed customer expectations and Consistently deliver client satisfaction.</p>
<div class="btn" style="left:722px;top:918px;width:108px;height:38px;font-size:12px">READ MORE</div>

<div class="abs split" style="left:123px;width:467px">
  <div class="photo" role="img" aria-label="Photograph of a hedge-lined garden walkway" style="left:0;width:204px;background:linear-gradient(90deg,#3e6a2a,#6d9a3a 60%,#c58a3a)"></div>
  <div class="body" style="left:204px;width:263px">
    <h3 style="left:24px;top:54px">COMMERCIAL</h3>
    <p style="left:20px;top:88px;width:222px">Lorem ipsum dolor sit amet, consectetur adipiscing elit, sed do eiusmod tempor inci didunt ut labore et dolore magna aliqua. Quis ipsum suspendisse.</p>
    <div class="btn" style="left:20px;top:160px;width:170px;height:34px;font-size:10.5px">COMMERCIAL SERVICES</div>
  </div>
</div>
<div class="abs split" style="left:610px;width:468px">
  <div class="body" style="left:0;width:263px">
    <h3 style="left:49px;top:54px">RESIDENTIAL</h3>
    <p style="left:45px;top:88px;width:212px">Lorem ipsum dolor sit amet, consectetur adipiscing elit, sed do eiusmod tempor inci didunt ut labore et dolore magna aliqua. Quis ipsum suspendisse.</p>
    <div class="btn" style="left:45px;top:160px;width:170px;height:34px;font-size:10.5px">RESIDENTIAL SERVICES</div>
  </div>
  <div class="photo" role="img" aria-label="Photograph of a rooftop garden with a wooden deck path" style="left:263px;width:205px;background:linear-gradient(180deg,#8fb3d8,#4f7a3c 45%,#7a6a50)"></div>
</div>
<svg class="abs" style="left:566px;top:1183px" width="66" height="66" viewBox="0 0 66 66">
  <circle cx="33" cy="33" r="30" fill="url(#frameGold)" stroke="#fff" stroke-width="3"/>
</svg>

<div class="section-title" style="top:1380px">OUR SERVICES</div>

<svg width="0" height="0" style="position:absolute">
  <defs>
    <symbol id="arrow" viewBox="0 0 18 10">
      <line x1="0" y1="5" x2="16" y2="5" stroke="currentColor" stroke-width="1.5"/>
      <polyline points="11,1 16,5 11,9" fill="none" stroke="currentColor" stroke-width="1.5"/>
    </symbol>
  </defs>
</svg>

<div class="svc" style="left:123px;top:1440px;width:304px;height:285px">
  <div class="img" role="img" aria-label="Photograph of a rock garden with shaped conifers" style="height:185px;background:linear-gradient(180deg,#3e5a3a,#6a7a5c 55%,#8a8676)"></div>
  <div class="badge" style="top:152px"></div>
  <div class="name" style="top:229px">Custom Built Landscape</div>
  <svg class="arrow" style="top:255px;color:#d6a92c" width="18" height="10"><use href="#arrow"/></svg>
</div>
<div class="svc featured" style="left:450px;top:1440px;width:297px;height:285px">
  <div class="img" role="img" aria-label="Black and white photograph of water pouring from a watering can onto flowers" style="height:185px;background:linear-gradient(180deg,#2a2a2a,#7b7b7b 60%,#bdbdbd)"></div>
  <div class="badge light" style="top:152px"></div>
  <div class="name" style="top:229px">Landscape Irrigation</div>
  <svg class="arrow" style="top:255px;color:#1b1b1b" width="18" height="10"><use href="#arrow"/></svg>
</div>
<div class="svc" style="left:772px;top:1440px;width:303px;height:285px">
  <div class="img" role="img" aria-label="Photograph of a lit garden pond at dusk" style="height:185px;background:linear-gradient(180deg,#3f5b8c,#4f6a55 55%,#6c6a58)"></div>
  <div class="badge" style="top:152px"></div>
  <div class="name" style="top:229px">Landscape Lighting</div>
  <svg class="arrow" style="top:255px;color:#d6a92c" width="18" height="10"><use href="#arrow"/></svg>
</div>

<div class="svc" style="left:123px;top:1750px;width:304px;height:288px">
  <div class="img" role="img" aria-label="Photograph of a wooden garden staircase with railings" style="height:185px;background:linear-gradient(180deg,#3c6a2e,#6b4a3a 50%,#8a6a5a)"></div>
  <div class="badge" style="top:152px"></div>
  <div class="name" style="top:229px">Landscape Features, Fences</div>
  <svg class="arrow" style="top:255px;color:#d6a92c" width="18" height="10"><use href="#arrow"/></svg>
</div>
<div class="svc" style="left:447px;top:1750px;width:304px;height:288px">
  <div class="img" role="img" aria-label="Photograph of soil being dug for garden drainage" style="height:185px;background:linear-gradient(180deg,#4a5a32,#5a4636 55%,#6e6a60)"></div>
  <div class="badge" style="top:152px"></div>
  <div class="name" style="top:229px">Landscape Drainage and Control</div>
  <svg class="arrow" style="top:255px;color:#d6a92c" width="18" height="10"><use href="#arrow"/></svg>
</div>
<div class="svc" style="left:772px;top:1750px;width:303px;height:288px">
  <div class="img" role="img" aria-label="Photograph of a garden path with a flowering arbor and swing" style="height:185px;background:linear-gradient(180deg,#4f6a3a,#7a8a4a 50%,#8a8470)"></div>
  <div class="badge" style="top:152px"></div>
  <div class="name" style="top:229px">Landscape Design &amp; Philosophy</div>
  <svg class="arrow" style="top:255px;color:#d6a92c" width="18" height="10"><use href="#arrow"/></svg>
</div>

<div class="btn" style="left:510px;top:2067px;width:180px;height:39px">DISCOVER OUR SERVICE</div>

<div class="abs testi-band"></div>
<div class="section-title testi-title" style="top:2202px">TESTIMONIALS</div>
<div class="tnav" style="left:90px"><svg width="8" height="8" viewBox="0 0 8 8"><polyline points="5,1 2,4 5,7" fill="none" stroke="#b7861d" stroke-width="1.6"/></svg></div>
<div class="tnav" style="left:1090px"><svg width="8" height="8" viewBox="0 0 8 8"><polyline points="3,1 6,4 3,7" fill="none" stroke="#b7861d" stroke-width="1.6"/></svg></div>

<div class="tcard" style="left:123px">
  <div class="avatar" role="img" aria-label="Client portrait"></div>
  <div class="who">Tomas Reyes</div><div class="stars">★★★★★</div>
  <p>Lorem Ipsum is simply dummy text of the printing and typesetting industry. Lorem Ipsum has been the industry's standard dummy text ever since the 1500s, when an unknown printer took a galley of type and scrambled it to make a type specimen book....</p>
  <div class="quote">”</div>
</div>
<div class="tcard" style="left:447px">
  <div class="avatar" role="img" aria-label="Client portrait"></div>
  <div class="who">Tomas Reyes</div><div class="stars">★★★★★</div>
  <p>Lorem Ipsum is simply dummy text of the printing and typesetting industry. Lorem Ipsum has been the industry's standard dummy text ever since the 1500s, when an unknown printer took a galley of type and scrambled it to make a type specimen book....</p>
  <div class="quote">”</div>
</div>
<div class="tcard" style="left:772px">
  <div class="avatar" role="img" aria-label="Client portrait"></div>
  <div class="who">Tomas Reyes</div><div class="stars">★★★★★</div>
  <p>Lorem Ipsum is simply dummy text of the printing and typesetting industry. Lorem Ipsum has been the industry's standard dummy text ever since the 1500s, when an unknown printer took a galley of type and scrambled it to make a type specimen book....</p>
</div>

<div class="section-title" style="top:2590px">OUR PROJECTS</div>
<div class="proj" style="left:123px;top:2650px"><div class="img" role="img" aria-label="Photograph of a terraced hillside garden" style="background:linear-gradient(180deg,#4a4a3a,#5e7a3a 60%,#3e4a2e)"></div><div class="label">South Slope Gardenl</div></div>
<div class="proj" style="left:447px;top:2650px"><div class="img" role="img" aria-label="Photograph of a white bench on a garden path" style="background:linear-gradient(180deg,#6a3a2a,#4f7a3a 45%,#8a9a6a)"></div><div class="label">Naturalistic Garden Path</div></div>
<div class="proj" style="left:772px;top:2650px"><div class="img" role="img" aria-label="Photograph of colourful flower beds in a townhouse garden" style="background:linear-gradient(180deg,#4a6a3a,#8a4a5a 50%,#3e5a2e)"></div><div class="label">Carroll Gardens Townhouse Garden</div></div>
<div class="proj" style="left:123px;top:2893px"><div class="img" role="img" aria-label="Photograph of a stone path through flowering shrubs" style="background:linear-gradient(180deg,#5a8a3a,#b04a7a 45%,#6a9a3a)"></div><div class="label">Rustic Rooftop Garden</div></div>
<div class="proj" style="left:447px;top:2893px"><div class="img" role="img" aria-label="Photograph of a front yard with geometric planting beds" style="background:linear-gradient(180deg,#6a6a6a,#5a7a3a 55%,#4a4a42)"></div><div class="label">Kensington Front Yard Planting</div></div>
<div class="proj" style="left:772px;top:2893px"><div class="img" role="img" aria-label="Photograph of a paved path between green shrubs" style="background:linear-gradient(180deg,#8aa86a,#4f7a3a 50%,#8a8a80)"></div><div class="label">Brooklyn Heights Townhouse Garden</div></div>
<div class="btn" style="left:519px;top:3142px;width:162px;height:39px">VIEW ALL PROJECTS</div>

<div class="abs contact-bg"></div>
<div class="abs contact-title h-serif">GET IN TOUCH</div>
<p class="abs contact-sub">Greenmark Landscape Management, Inc. offers green solutions for our clients. We strive to make responsible changes, using permeable</p>
<div class="field" style="top:3349px">Name</div>
<div class="field" style="top:3394px">Email</div>
<div class="field" style="top:3438px">Phone</div>
<div class="field" style="top:3483px">Address</div>
<div class="field" style="top:3526px;height:65px">Message</div>
<div class="btn" style="left:123px;top:3608px;width:108px;height:37px;font-size:12px">SUBMIT</div>

<svg class="abs" style="left:725px;top:3222px" width="350" height="466" viewBox="0 0 350 462" role="img" aria-label="Photograph of a gardener holding a clipboard in a plant nursery, framed in a gold drop shape">
  <defs>
    <linearGradient id="contactPhoto" x1="0" y1="0" x2="0" y2="1">
      <stop offset="0" stop-color="#5a6a3a"/><stop offset="0.5" stop-color="#6e5a4a"/><stop offset="1" stop-color="#3e4a2a"/>
    </linearGradient>
  </defs>
  <path d="M175 4 C240 100 346 190 346 290 A171 171 0 0 1 4 290 C4 190 110 100 175 4 Z" fill="#fff" stroke="url(#frameGold)" stroke-width="9"/>
  <path d="M175 40 C228 120 318 200 318 290 A143 143 0 0 1 32 290 C32 200 122 120 175 40 Z" fill="url(#contactPhoto)"/>
</svg>

<div class="abs footer">
  <div class="logo" style="left:126px;top:34px;width:100px;text-align:left">
    <svg width="22" height="30" viewBox="0 0 22 30" style="margin-left:38px"><circle cx="11" cy="15" r="9" fill="none" stroke="#d6a92c" stroke-width="1.4"/></svg>
    <div style="font-size:13px;letter-spacing:5px;line-height:18px">BRIMSETT</div>
    <div style="font-size:7px;letter-spacing:3.6px;line-height:10px">GARDENING</div>
  </div>
  <p class="about-f">Lorem ipsum dolor sit amet, consectetur adipiscing elit. Quisque id fringilla odio, non efficitur dui.</p>

  <div class="rule" style="left:365px"></div>
  <div class="rule" style="left:602px"></div>
  <div class="rule" style="left:890px"></div>

  <h4 style="left:430px">QUICK LINKS</h4>
  <div class="links">
    <a style="left:430px;top:80px">Home</a>
    <a style="left:430px;top:100px">Services</a>
    <a style="left:430px;top:120px">About Us</a>
    <a style="left:430px;top:140px">Our Projects</a>
    <a style="left:430px;top:160px">Contact Us</a>
  </div>

  <h4 style="left:668px">CONTACT US</h4>
  <div class="line" style="left:668px;top:78px"><span class="dot"></span>(405) 555-0148</div>
  <div class="line" style="left:668px;top:109px"><span class="dot"></span>info@brimsettgardening.com</div>
  <div class="line" style="left:668px;top:140px"><span class="dot"></span>1187 Larkspur Ave #310<br>Oklahoma City, OK 73120</div>

  <h4 style="left:963px">FOLLOW US</h4>
  <div class="line" style="left:963px;top:80px"><span class="dot"></span>Newsfeed</div>
  <div class="line" style="left:963px;top:110px"><span class="dot"></span>Updates</div>
  <div class="line" style="left:963px;top:140px"><span class="dot"></span>Network</div>
</div>
<div class="abs copyright gold-grad">©2024 Brimsett Gardening, all rights reserved</div>

</body>
</html>
```